Custom Seed Packet design for Flower Farm

We need a design for our seeds packets.
The design will be a kind of "fill in the blanks" as we need the design to be adaptable for multiple varieties of seed. We will be using the design for a rubber stamp.
Our seed packets are 90x90mm in size.
Black logo only. No colour required.
A vintage botanical influence is desired.
Will need to include the following info,
"Wrenfield Gable Co logo" , "Seeds", "Plant Type", "Variety", "Harvested"

```html
<!DOCTYPE html>
<html lang="en">
<head>
<meta charset="utf-8">
<title>Seed Packet Label</title>
<link rel="stylesheet" href="https://fonts.googleapis.com/css2?family=Dancing+Script:wght@700&family=Open+Sans:wght@400&display=swap">
<style>
  :root {
    --kraft: #d8c29c;
    --kraft-light: #e2cfaf;
    --ink: #1a1613;
    --ornament: #3a302a;
  }
  * { margin: 0; padding: 0; box-sizing: border-box; }
  html, body {
    width: 1122px;
    height: 1200px;
    overflow: hidden;
    background: #ffffff;
  }
  .canvas {
    position: relative;
    width: 1122px;
    height: 1200px;
    background: radial-gradient(ellipse at 50% 40%, var(--kraft-light), var(--kraft));
    font-family: "Open Sans", sans-serif;
    color: var(--ink);
  }
  .label-frame {
    position: absolute;
    left: 60px;
    top: 99px;
    width: 1002px;
    height: 1002px;
    border: 3px solid var(--ink);
  }
  .label-frame-inner {
    position: absolute;
    inset: 7px;
    border: 1.5px solid var(--ink);
  }
  .corner-ornament {
    position: absolute;
    width: 140px;
    height: 140px;
    background: radial-gradient(circle at var(--cx) var(--cy), var(--ornament) 0%, rgba(58,48,42,0.55) 35%, rgba(58,48,42,0) 75%);
    opacity: 0.6;
  }
  .corner-tl { top: 14px; left: 14px; --cx: 20%; --cy: 20%; }
  .corner-tr { top: 14px; right: 14px; --cx: 80%; --cy: 20%; }
  .corner-bl { bottom: 14px; left: 14px; --cx: 20%; --cy: 80%; }
  .corner-br { bottom: 14px; right: 14px; --cx: 80%; --cy: 80%; }
  .packet-title {
    position: absolute;
    top: 100px;
    left: 0;
    right: 0;
    text-align: center;
    font-family: "Dancing Script", cursive;
    font-weight: 700;
    font-size: 150px;
    line-height: 1;
  }
  .fill-fields {
    position: absolute;
    top: 370px;
    left: 100px;
    width: 810px;
    list-style: none;
  }
  .fill-field {
    display: flex;
    align-items: flex-end;
    height: 86px;
    font-size: 24px;
  }
  .fill-field-name { white-space: nowrap; padding-right: 4px; }
  .fill-field-line {
    flex: 1;
    border-bottom: 1.5px solid var(--ink);
    margin-bottom: 6px;
  }
  .brand-name {
    position: absolute;
    top: 790px;
    left: 0;
    right: 0;
    text-align: center;
    font-family: "Open Sans", sans-serif;
    font-weight: 400;
    font-size: 34px;
    letter-spacing: 1px;
    line-height: 1.5;
    color: var(--ink);
  }
</style>
</head>
<body>
  <main class="canvas">
    <section class="label-frame">
      <div class="label-frame-inner"></div>
      <div class="corner-ornament corner-tl" role="img" aria-label="Vintage filigree corner ornament"></div>
      <div class="corner-ornament corner-tr" role="img" aria-label="Vintage filigree corner ornament"></div>
      <div class="corner-ornament corner-bl" role="img" aria-label="Vintage filigree corner ornament"></div>
      <div class="corner-ornament corner-br" role="img" aria-label="Vintage filigree corner ornament"></div>

      <h1 class="packet-title">Seeds</h1>

      <ul class="fill-fields">
        <li class="fill-field"><span class="fill-field-name">Plant Type</span><span class="fill-field-line"></span></li>
        <li class="fill-field"><span class="fill-field-name">Variety</span><span class="fill-field-line"></span></li>
        <li class="fill-field"><span class="fill-field-name">Harvested</span><span class="fill-field-line"></span></li>
      </ul>

      <p class="brand-name">Wrenfield Gable Co<br>Flower Farm</p>
    </section>
  </main>
</body>
</html>
```